Pain cream backed by Pro-Athletes "Glacier Ember"

Looking to revamp the label brand.
It's an all-natural pain gel. It heats then cools. Looking for a very sharp look that gets the point of the product use across.
Eveyrthing about the original label can be changed except for the text. It still needs to have the same information but can be any color, font whatever.,
I'll need pdf's and ai files of the design.
Label Size die line is attached.
Original Label is attached.

```html
<!DOCTYPE html>
<html lang="en">
<head>
<meta charset="utf-8">
<title>Glacier Ember – Label</title>
<link rel="stylesheet" href="https://fonts.googleapis.com/css2?family=Rubik:ital,wght@0,500;1,800&family=Roboto+Condensed:wght@500&display=swap">
<style>
  :root {
    --page: #ffffff;
    --ice-top: #ffffff;
    --ice-mid: #dfeaee;
    --ice-low: #bfd6dd;
    --ice-deep: #a9c7d0;
    --navy: #2e3356;
    --teal: #3f9fbd;
  }
  html, body {
    margin: 0;
    padding: 0;
    width: 1200px;
    height: 1200px;
    overflow: hidden;
    background: var(--page);
  }
  .canvas {
    position: relative;
    width: 1200px;
    height: 1200px;
  }
  .label {
    position: absolute;
    left: 390px;
    top: 100px;
    width: 420px;
    height: 1000px;
    overflow: hidden;
    box-shadow: 0 0 0 1px #e6ecef;
  }
  .label__frost {
    position: absolute;
    inset: 0;
    background: linear-gradient(180deg, var(--ice-top) 0%, var(--ice-top) 28%, var(--ice-mid) 55%, var(--ice-low) 80%, var(--ice-deep) 100%);
  }
  .brand-name {
    position: absolute;
    left: 40px;
    top: 955px;
    transform-origin: 0 0;
    transform: rotate(-90deg);
    margin: 0;
    font-family: "Rubik", sans-serif;
    font-weight: 500;
    font-size: 88px;
    line-height: 1;
    letter-spacing: 1px;
    color: var(--navy);
    white-space: nowrap;
  }
  .tagline {
    position: absolute;
    left: 165px;
    top: 60px;
    margin: 0;
    font-family: "Rubik", sans-serif;
    font-style: italic;
    font-weight: 800;
    font-size: 54px;
    line-height: 1.02;
    color: var(--teal);
    text-transform: uppercase;
  }
  .volume {
    position: absolute;
    left: 168px;
    top: 912px;
    margin: 0;
    font-family: "Roboto Condensed", sans-serif;
    font-weight: 500;
    font-size: 27px;
    line-height: 1;
    color: var(--navy);
  }
</style>
</head>
<body>
  <main class="canvas">
    <section class="label">
      <div class="label__frost" role="img" aria-label="Frosted ice texture fading from white at the top to pale glacier blue at the bottom"></div>
      <h1 class="brand-name">GLACIER EMBER</h1>
      <p class="tagline">Gets<br>you<br>back<br>up</p>
      <p class="volume">100ml (3.2oz)</p>
    </section>
  </main>
</body>
</html>
```